Business card design Needed for new logo / Construction business, home extensions and new builds

We need a business card design using our new logo files which i will attach to this project :)

We are a small construction business specialising in home extensions, new builds and property development. We are very ambitious and would appreciate professional and elegant designs for our new business card.

Very serious about using the services on MakerQuarry and recently acquired our new logo from here :)

Please get involved, i will feedback when i can as i am very busy but can respond daily, thanks

Target Market(s)

People that want to build onto their houses, new building developments or adding too their existing property

Industry/Entity Type

Construction

Contact Information for Business Card

Renwick Tolliver Construction, Lionel Ashby (Managing Director), Tel 07822254961, email - info@renwick-tolliver, www.renwick-tolliver.co.uk

Colors

Designer to choose colors to be used in the design.

Requirements
Must have
• I like a deep grey on the back please. A lot of you have provided black from and back, try mixing things up a little. The black looks cool 😎 Thanks

```html
<!DOCTYPE html>
<html lang="en">
<head>
<meta charset="utf-8">
<title>Renwick Tolliver Construction – Business Cards</title>
<link rel="stylesheet" href="https://fonts.googleapis.com/css2?family=Cinzel:wght@600&family=Poppins:wght@400&display=swap">
<style>
  :root {
    --backdrop: #6b6b6b;
    --card-dark: #1e1e1e;
    --gold-deep: #a8700c;
    --gold-mid: #d3a449;
    --gold-light: #f6d283;
    --silver: #e6e6e6;
    --ink: #1a1a1a;
    --brand-gold: #d9aa3f;
  }
  * { box-sizing: border-box; margin: 0; padding: 0; }
  html, body { width: 1075px; height: 1200px; overflow: hidden; }
  body { background: var(--backdrop); position: relative; font-family: "Poppins", sans-serif; }

  .card {
    position: absolute;
    left: 207px;
    width: 663px;
    height: 396px;
    background: var(--card-dark);
    box-shadow: 2px 3px 3px rgba(0,0,0,0.45);
    overflow: hidden;
  }
  .card--front { top: 187px; }
  .card--back { top: 637px; }
  .card__art { position: absolute; inset: 0; width: 100%; height: 100%; }

  .holder { position: absolute; left: 34px; top: 128px; color: var(--ink); }
  .holder__name { font-family: "Cinzel", serif; font-weight: 600; font-size: 23px; letter-spacing: 0.3px; line-height: 1; }
  .holder__role { font-size: 15px; margin-top: 4px; line-height: 1; text-transform: uppercase; }

  .contacts { position: absolute; left: 36px; top: 207px; list-style: none; color: var(--ink); font-size: 18px; line-height: 24px; }
  .contacts li { display: flex; align-items: center; gap: 6px; }
  .contacts svg { width: 16px; height: 16px; flex: none; }

  .address { position: absolute; left: 36px; top: 305px; color: var(--ink); font-size: 18px; line-height: 24px; font-style: normal; }

  .brand {
    position: absolute;
    text-align: center;
    font-family: "Cinzel", serif;
    font-weight: 600;
    color: var(--brand-gold);
    line-height: 1.15;
  }
  .card--front .brand { left: 340px; width: 290px; top: 170px; font-size: 27px; }
  .card--back .brand { left: 170px; width: 323px; top: 240px; font-size: 30px; }
  .brand__mark { display: block; width: 16px; height: 16px; background: var(--brand-gold); margin: 0 auto 12px; }
</style>
</head>
<body>

<section class="card card--front" aria-label="Business card front">
  <svg class="card__art" viewBox="0 0 738 440" preserveAspectRatio="none" aria-hidden="true">
    <defs>
      <linearGradient id="gold-front" x1="0" y1="0" x2="1" y2="0">
        <stop offset="0" stop-color="#c8962f"/>
        <stop offset="0.45" stop-color="#f6d283"/>
        <stop offset="0.75" stop-color="#e0b564"/>
        <stop offset="1" stop-color="#a8700c"/>
      </linearGradient>
    </defs>
    <polygon points="0,0 220,0 470,440 0,440" fill="url(#gold-front)"/>
    <polygon points="224,0 232,0 484,440 476,440" fill="#e6e6e6"/>
  </svg>

  <div class="holder">
    <h1 class="holder__name">LIONEL ASHBY</h1>
    <p class="holder__role">Managing Director</p>
  </div>

  <ul class="contacts">
    <li><svg viewBox="0 0 16 16"><path d="M4 1.5l2.5 3-1.5 1.5c.8 2 2.5 3.7 4.5 4.5l1.5-1.5 3 2.5-1.5 2.5C7.5 14 2 8.5 1.5 3z" fill="#1a1a1a"/></svg>07822254961</li>
    <li><svg viewBox="0 0 16 16"><rect x="1" y="3.5" width="14" height="9" fill="#1a1a1a"/><path d="M1.5 4l6.5 5 6.5-5" stroke="#e0b564" stroke-width="1.2" fill="none"/></svg>info@renwick-tolliver</li>
    <li><svg viewBox="0 0 16 16" fill="none" stroke="#1a1a1a" stroke-width="1.3"><circle cx="8" cy="8" r="6.5"/><ellipse cx="8" cy="8" rx="3" ry="6.5"/><path d="M1.5 8h13M2.5 5h11M2.5 11h11"/></svg>www.renwick-tolliver.co.uk</li>
  </ul>

  <address class="address">421, Address line goes here<br>45452,Country Name</address>

  <div class="brand">
    <span class="brand__mark" aria-hidden="true"></span>
    RENWICK TOLLIVER<br>CONSTRUCTION
  </div>
</section>

<section class="card card--back" aria-label="Business card back">
  <svg class="card__art" viewBox="0 0 738 440" preserveAspectRatio="none" aria-hidden="true">
    <defs>
      <linearGradient id="gold-back" x1="0" y1="0" x2="1" y2="0">
        <stop offset="0" stop-color="#c8962f"/>
        <stop offset="0.5" stop-color="#f6d283"/>
        <stop offset="1" stop-color="#a8700c"/>
      </linearGradient>
    </defs>
    <polygon points="505,0 738,0 738,285" fill="url(#gold-back)"/>
    <polygon points="485,0 494,0 738,296 738,306" fill="#e6e6e6"/>
    <polygon points="0,321 0,440 92,440" fill="url(#gold-back)"/>
    <polygon points="0,303 0,313 104,440 113,440" fill="#e6e6e6"/>
  </svg>

  <div class="brand">
    <span class="brand__mark" aria-hidden="true"></span>
    RENWICK TOLLIVER<br>CONSTRUCTION
  </div>
</section>

</body>
</html>
```